Harrowgate Care Assurance Ltd needs a business card and logo

We need a logo for documents, invoices etc and a business card to match. We are a health auditing, training and consulting company based in NZ and working in both Australia and NZ. We ensure health organisations meet all their compliance requirements and develop expertise in the health auditing sector. The design should in some way reflect either symbols for quality management in the health sector.

Target Market(s)

Health providers and those wishing to increase their capability in meeting and understanding compliance requirements

Industry/Entity Type

Business

Contact Information for Business Card

Logo plus contact details

Logo Text

Health auditing, consultancy and training

Requirements
Must have
• Name and contact details director: Marla Fenwick, mfenwick@hca-example.co.nz, PO Box 318, Warkworth, NZ, cell +6427391652

```html
<!DOCTYPE html>
<html lang="en">
<head>
<meta charset="utf-8">
<title>Harrowgate Care Assurance Ltd – Business Card</title>
<link href="https://fonts.googleapis.com/css2?family=Open+Sans:wght@400;600;700&display=swap" rel="stylesheet">
<style>
  :root {
    --backdrop: #2b2b2b;
    --brand-blue: #1a7cc4;
    --brand-blue-deep: #0a5a9c;
    --brand-blue-light: #1f86cf;
    --ink: #333333;
    --paper: #ffffff;
    --rule: #2a2a2a;
  }
  html, body {
    margin: 0;
    padding: 0;
    width: 1200px;
    height: 1002px;
    overflow: hidden;
    background: var(--backdrop);
    font-family: "Open Sans", Arial, sans-serif;
  }
  .canvas {
    position: relative;
    width: 1200px;
    height: 1002px;
  }
  .card {
    position: absolute;
    left: 275px;
    width: 619px;
    height: 379px;
    border-radius: 13px;
    overflow: hidden;
  }
  .card--front {
    top: 100px;
    background: radial-gradient(ellipse at 50% 50%, #1a84cc 0%, #0f6fb6 40%, var(--brand-blue-deep) 100%);
  }
  .card--back {
    top: 510px;
    background: var(--paper);
  }
  .logo {
    position: absolute;
    display: flex;
    align-items: center;
    gap: 16px;
  }
  .logo__disc {
    border-radius: 50%;
    flex: none;
  }
  .logo__name {
    font-weight: 400;
    font-size: 21px;
    line-height: 1.25;
    letter-spacing: 1.5px;
    text-transform: uppercase;
  }
  .card--front .logo { left: 139px; top: 137px; }
  .card--front .logo__disc { width: 108px; height: 108px; background: var(--paper); }
  .card--front .logo__name { color: var(--paper); }

  .card--back .logo { left: 100px; top: 80px; }
  .card--back .logo__disc {
    width: 124px; height: 124px;
    background: radial-gradient(circle at 40% 35%, #2a9ae0 0%, var(--brand-blue) 55%, var(--brand-blue-deep) 100%);
  }
  .card--back .logo__name { color: var(--ink); }

  .holder {
    position: absolute;
    top: 230px;
    left: 0;
    width: 100%;
    text-align: center;
    font-weight: 700;
    font-size: 16px;
    letter-spacing: 0.5px;
    color: var(--brand-blue-deep);
    text-transform: uppercase;
  }
  .holder-rule {
    position: absolute;
    top: 262px;
    left: 36px;
    right: 37px;
    height: 2px;
    background: var(--brand-blue);
  }
  .contact {
    position: absolute;
    left: 43px;
    top: 289px;
    font-size: 15.5px;
    color: var(--ink);
    line-height: 22px;
  }
  .contact__row { display: flex; align-items: center; gap: 6px; }
  .contact__icon { width: 13px; height: 13px; flex: none; }
  .address {
    position: absolute;
    right: 38px;
    top: 313px;
    font-size: 15.5px;
    color: var(--ink);
  }
  .footer-rule {
    position: absolute;
    left: 0; right: 0;
    top: 353px;
    height: 5px;
    background: var(--rule);
  }
  .footer-band {
    position: absolute;
    left: 0; right: 0;
    top: 358px;
    bottom: 0;
    background: var(--brand-blue-light);
  }
</style>
</head>
<body>
<main class="canvas">
  <section class="card card--front" aria-label="Card front">
    <div class="logo">
      <span class="logo__disc"></span>
      <span class="logo__name">Harrowgate Care<br>Assurance Ltd</span>
    </div>
  </section>

  <section class="card card--back" aria-label="Card back">
    <div class="logo">
      <span class="logo__disc"></span>
      <span class="logo__name">Harrowgate Care<br>Assurance Ltd</span>
    </div>

    <div class="holder">Marla Fenwick</div>
    <div class="holder-rule"></div>

    <div class="contact">
      <div class="contact__row">
        <svg class="contact__icon" viewBox="0 0 13 13" aria-hidden="true">
          <rect x="3" y="0.5" width="7" height="12" rx="1.3" fill="none" stroke="#1a7cc4" stroke-width="1.3"/>
          <rect x="4.3" y="2" width="4.4" height="7.5" fill="#1a7cc4"/>
        </svg>
        <span>+6427391652</span>
      </div>
      <div class="contact__row">
        <svg class="contact__icon" viewBox="0 0 13 13" aria-hidden="true">
          <rect x="0.5" y="2.5" width="12" height="8.5" fill="#1a7cc4"/>
          <path d="M0.8 2.8 L6.5 7.3 L12.2 2.8" fill="none" stroke="#ffffff" stroke-width="1"/>
        </svg>
        <span>mfenwick@hca-example.co.nz</span>
      </div>
    </div>

    <div class="address">PO Box 318, Warkworth, NZ</div>

    <div class="footer-rule"></div>
    <div class="footer-band"></div>
  </section>
</main>
</body>
</html>
```